Design a business card
Business name: Harbourline Growth Advisory
Improving Business Profitibility

- An Overview of the Business & Service:

Business Performance Consulting

- The Target Market: Small to medium-sized business

- Design Specifics:
White card, blue ink, moon eclipse

No Logo

Target Market(s)

Small to medium-sized business

Font styles to use
Sans Serif

```html
<!DOCTYPE html>
<html lang="en">
<head>
<meta charset="utf-8">
<title>Harbourline Growth Advisory – Business Card</title>
<link href="https://fonts.googleapis.com/css2?family=Oswald:wght@500;600&family=Open+Sans:wght@400;600&display=swap" rel="stylesheet">
<style>
  :root {
    --backdrop: #2a2a2d;
    --card: #ffffff;
    --card-edge: #e2e2e6;
    --ink-blue: #1f58b4;
    --text-dark: #2e2e33;
    --text-muted: #6f6f76;
    --rule: #cfd3da;
    --photo-fill: #c4693a;
  }
  * { box-sizing: border-box; margin: 0; padding: 0; }
  html, body { width: 1200px; height: 900px; overflow: hidden; }
  body {
    background: var(--backdrop);
    font-family: "Open Sans", Arial, sans-serif;
    position: relative;
  }
  .card {
    position: absolute;
    top: 307px;
    width: 500px;
    height: 286px;
    background: var(--card);
    border: 1px solid var(--card-edge);
    border-radius: 22px;
    box-shadow: 0 18px 40px rgba(0,0,0,.45);
    overflow: hidden;
  }
  .card--front { left: 70px; }
  .card--back { left: 630px; }

  /* front */
  .eclipse-photo {
    position: absolute;
    left: 50%;
    top: 54px;
    width: 140px;
    height: 116px;
    margin-left: -70px;
    border-radius: 8px;
    background: var(--photo-fill);
  }
  .tagline {
    position: absolute;
    left: 0; right: 0;
    top: 200px;
    text-align: center;
    font-family: "Oswald", Arial, sans-serif;
    font-weight: 500;
    font-size: 15px;
    letter-spacing: 1.5px;
    color: var(--text-muted);
    text-transform: uppercase;
  }

  /* back */
  .brand {
    position: absolute;
    right: 30px;
    top: 30px;
    display: flex;
    align-items: center;
    gap: 12px;
  }
  .brand__dot {
    width: 34px; height: 34px;
    border-radius: 50%;
    background: var(--ink-blue);
    flex: none;
  }
  .brand__name {
    font-family: "Oswald", Arial, sans-serif;
    font-weight: 600;
    font-size: 21px;
    line-height: 1.1;
    letter-spacing: .5px;
    color: var(--ink-blue);
    text-transform: uppercase;
  }
  .divider {
    position: absolute;
    left: 26px; right: 26px;
    top: 112px;
    height: 1px;
    background: var(--rule);
  }
  .person {
    position: absolute;
    left: 30px;
    top: 128px;
  }
  .person__name {
    font-family: "Oswald", Arial, sans-serif;
    font-weight: 600;
    font-size: 19px;
    color: var(--ink-blue);
    text-transform: uppercase;
    letter-spacing: .3px;
    line-height: 1.15;
  }
  .person__role {
    font-size: 13px;
    color: var(--text-dark);
    padding-bottom: 8px;
    border-bottom: 1px solid var(--rule);
    width: 170px;
  }
  .contact { list-style: none; margin-top: 8px; }
  .contact li {
    display: flex;
    align-items: center;
    gap: 8px;
    font-size: 13px;
    line-height: 19px;
    color: var(--text-dark);
  }
  .contact svg { width: 11px; height: 11px; fill: var(--ink-blue); flex: none; }
  .address {
    position: absolute;
    right: 30px;
    top: 132px;
    text-align: right;
    font-size: 13px;
    line-height: 19px;
    color: var(--text-dark);
    font-style: normal;
  }
</style>
</head>
<body>

<section class="card card--front">
  <div class="eclipse-photo" role="img" aria-label="Photograph of a copper-red lunar eclipse moon"></div>
  <p class="tagline">Improving Business Profitibility</p>
</section>

<section class="card card--back">
  <div class="brand">
    <span class="brand__dot"></span>
    <span class="brand__name">Harbourline Growth<br>Advisory</span>
  </div>
  <div class="divider"></div>

  <div class="person">
    <p class="person__name">Desmond R Akerly</p>
    <p class="person__role">Managing Director</p>
    <ul class="contact">
      <li><svg viewBox="0 0 12 12"><path d="M1 4c0-2 1.5-3 5-3s5 1 5 3l-2 1-1-2H4L3 5zM3 6h6l1 5H2z"/></svg>044-555 210 384</li>
      <li><svg viewBox="0 0 12 12"><path d="M3 0h6v12H3zM4 1.5v8h4v-8z"/></svg>044-555 210 384</li>
      <li><svg viewBox="0 0 12 12"><path d="M0 2h12v8H0zM1 3l5 4 5-4z"/></svg>info@harbourline-advisory.com</li>
      <li><svg viewBox="0 0 12 12"><circle cx="6" cy="6" r="5.5"/></svg>www.harbourline-advisory.com</li>
    </ul>
  </div>

  <address class="address">48 Quayside Lane, Suite 9<br>Portmere, 204817</address>
</section>

</body>
</html>
```